I need a business card designed using the logo provided either vertical or horizontal......Harbourline Property Group is an Australian based real estate company that caters for the upper end of the market so the design of the business card "must reflect" the companies image!!
Colour combinations are optional but "must be realistic" and must be able to be accurately useable CMYK colours.
Please consider that any colours used "must be able to be used" and be suitable in following designs for "pull out banner signs" and "real estate signs".
The colours and the font in the attached designs are for example and other combinations are encouraged.
Target Market(s)
The High End of the Australian real estate market
Industry/Entity Type
Business
Contact Information for Business Card
Logo - Business Name - Director + Licensed Real Estate Agent - Mobile Number (Cell Phone) - Business Number - Fax - Email Address - Web address
Requirements
Must have
- Designs and colours (CMYK) that can easily be interpreted by an Australian printer.
Nice to have
- Some alternative ideas on colour and font..........the ones provided are ok and have been provided as an example but I am looking for alternative ideas
Should not have
- Loud, overly bright colours. Designs that do not reflect the professional standards of the business.
- Designs that look good on a computer monitor but can not be re-created on a printing press.............this is most important when it comes to shading etc.

```html
<!DOCTYPE html>
<html lang="en">
<head>
<meta charset="utf-8">
<title>Harbourline Property Group – Business Card</title>
<link rel="stylesheet" href="https://fonts.googleapis.com/css2?family=Open+Sans:wght@400;600;700&display=swap">
<style>
  :root {
    --backdrop: #3b3532;
    --card: #2c2c2d;
    --card-glow: #4a4a4b;
    --accent: #3d9fd6;
    --text-light: #e6e6e6;
    --text-muted: #c9c9c9;
  }
  * { margin: 0; padding: 0; box-sizing: border-box; }
  html, body {
    width: 1200px;
    height: 900px;
    overflow: hidden;
    background: var(--backdrop);
    font-family: "Open Sans", Arial, sans-serif;
  }
  .stage {
    position: relative;
    width: 1200px;
    height: 900px;
  }
  .card {
    position: absolute;
    top: 300px;
    width: 520px;
    height: 300px;
    border-radius: 3px;
    background: radial-gradient(ellipse at 50% 40%, var(--card-glow) 0%, var(--card) 70%);
    box-shadow: 0 8px 24px rgba(0,0,0,0.45);
  }
  .card--front { left: 50px; }
  .card--back { left: 630px; }

  /* Front */
  .front-brand {
    position: absolute;
    left: 36px;
    top: 112px;
    width: 170px;
    display: flex;
    align-items: center;
    gap: 10px;
  }
  .front-brand__square {
    flex: none;
    width: 14px;
    height: 14px;
    background: var(--accent);
  }
  .front-brand__name {
    color: var(--accent);
    font-weight: 700;
    font-size: 19px;
    line-height: 1.2;
    text-transform: uppercase;
  }
  .details {
    position: absolute;
    left: 250px;
    top: 52px;
    color: var(--text-light);
  }
  .details__name {
    color: var(--accent);
    font-weight: 600;
    font-size: 17px;
    letter-spacing: 0.5px;
    text-transform: uppercase;
    line-height: 1.1;
  }
  .details__role {
    font-size: 13px;
    color: var(--text-muted);
    margin-bottom: 20px;
  }
  .details__address {
    font-size: 13px;
    line-height: 1.35;
    color: var(--text-muted);
    margin-bottom: 18px;
  }
  .contact-list { list-style: none; }
  .contact-list li {
    display: flex;
    align-items: center;
    gap: 9px;
    font-size: 13px;
    line-height: 19px;
    color: var(--text-light);
  }
  .contact-list svg { width: 11px; height: 11px; fill: var(--accent); flex: none; }

  /* Back */
  .back-brand {
    position: absolute;
    inset: 0;
    display: flex;
    align-items: center;
    justify-content: center;
    gap: 14px;
  }
  .back-brand__square {
    width: 22px;
    height: 22px;
    background: var(--accent);
  }
  .back-brand__name {
    color: var(--text-light);
    font-weight: 700;
    font-size: 28px;
    line-height: 1.15;
    text-transform: uppercase;
    letter-spacing: 0.5px;
  }
</style>
</head>
<body>
<main class="stage">
  <section class="card card--front" aria-label="Business card front">
    <div class="front-brand">
      <span class="front-brand__square"></span>
      <span class="front-brand__name">Harbourline Property Group</span>
    </div>
    <div class="details">
      <p class="details__name">Marcus Hale</p>
      <p class="details__role">Managing Director</p>
      <p class="details__address">48 Esplanade Quay<br>Sydney NSW, 2000.</p>
      <ul class="contact-list">
        <li>
          <svg viewBox="0 0 12 12" aria-hidden="true"><path d="M2.5 1 4.5 1 5 3.5 3.8 4.5C4.5 6 6 7.5 7.5 8.2L8.5 7 11 7.5 11 9.5C11 10.3 10.3 11 9.5 11 5 11 1 7 1 2.5 1 1.7 1.7 1 2.5 1Z"/></svg>
          <span>0412 847 395</span>
        </li>
        <li>
          <svg viewBox="0 0 12 12" aria-hidden="true"><path d="M3 1h6v3H3zM1 5h10v6H1zM3 7h2v1H3zM6 7h3v1H6z"/></svg>
          <span>02 9455 7120</span>
        </li>
        <li>
          <svg viewBox="0 0 12 12" aria-hidden="true"><path d="M1 2.5h10v7H1zM1.5 3 6 6.5 10.5 3" stroke="#2c2c2d" stroke-width="1"/></svg>
          <span>info@harbourline.com.au</span>
        </li>
        <li>
          <svg viewBox="0 0 12 12" aria-hidden="true"><path d="M4.5 7.5 7.5 4.5M5.5 3 7 1.5a2 2 0 0 1 3 3L8.5 6M6.5 9 5 10.5a2 2 0 0 1-3-3L3.5 6" fill="none" stroke="#3d9fd6" stroke-width="1.4"/></svg>
          <span>www.harbourlinegroup.com.au</span>
        </li>
      </ul>
    </div>
  </section>

  <section class="card card--back" aria-label="Business card back">
    <div class="back-brand">
      <span class="back-brand__square"></span>
      <span class="back-brand__name">Harbourline<br>Property Group</span>
    </div>
  </section>
</main>
</body>
</html>
```